Business Card Design

I give lessons and clinics for dressage riders
I would like the design to be an outline (with broad lines) of a dressage horse and rider with in background of whole card with print over top tan or parchment card with burgundy print

Industry/Entity Type

Business

Contact Information for Business Card

Dale Ferrin
612-374-2059
Classical dressage training for the modern American
Clinics, lessons, training level -Prix St. George

Requirements
Must have
• broad lined outline of dressage horse and rider

```html
<!DOCTYPE html>
<html lang="en">
<head>
<meta charset="UTF-8">
<title>Dale Ferrin — Classical Dressage Training</title>
<link rel="stylesheet" href="https://fonts.googleapis.com/css2?family=Cinzel:wght@700;900&display=swap">
<style>
  :root {
    --parchment-center: #ecd9b8;
    --parchment-mid: #dfc29f;
    --parchment-edge: #c08c7c;
    --burgundy-deep: #4a0d22;
    --burgundy: #5c1429;
    --burgundy-soft: #6e1f33;
    --rose-art: #9e5560;
    --rose-art-light: #b8747a;
  }
  * { margin: 0; padding: 0; box-sizing: border-box; }
  html, body {
    width: 1200px;
    height: 693px;
    overflow: hidden;
    background: var(--parchment-mid);
  }
  .business-card {
    position: relative;
    width: 1200px;
    height: 693px;
    overflow: hidden;
    background:
      radial-gradient(ellipse 75% 70% at 50% 48%, var(--parchment-center) 0%, var(--parchment-mid) 62%, var(--parchment-edge) 100%);
    font-family: "Cinzel", "Times New Roman", serif;
  }
  .card-frame {
    position: absolute;
    inset: 0;
    width: 1200px;
    height: 693px;
  }
  .card-frame path {
    fill: none;
    stroke: var(--burgundy-deep);
    stroke-width: 8;
    stroke-linecap: square;
  }
  .rider-artwork {
    position: absolute;
    left: 770px;
    top: 12px;
    width: 318px;
    height: 520px;
    background: linear-gradient(170deg, var(--rose-art-light) 0%, var(--rose-art) 60%, var(--rose-art-light) 100%);
    opacity: 0.85;
    border-radius: 40% 30% 10% 20% / 20% 15% 5% 10%;
  }
  .hoof-artwork {
    position: absolute;
    left: 812px;
    top: 610px;
    width: 294px;
    height: 48px;
    background: linear-gradient(90deg, var(--rose-art), var(--rose-art-light));
    opacity: 0.8;
    border-radius: 16px;
  }
  .contact-block {
    position: absolute;
    left: 85px;
    top: 398px;
    color: var(--burgundy);
  }
  .trainer-name {
    font-size: 54px;
    font-weight: 700;
    line-height: 60px;
    letter-spacing: 1px;
  }
  .trainer-phone {
    font-size: 52px;
    font-weight: 700;
    line-height: 64px;
    letter-spacing: 1px;
  }
  .services {
    margin-top: 6px;
    font-size: 26px;
    font-weight: 700;
    line-height: 35px;
    color: var(--burgundy-soft);
    letter-spacing: 0.4px;
    white-space: nowrap;
  }
</style>
</head>
<body>
  <main class="business-card">
    <svg class="card-frame" viewBox="0 0 1200 693" aria-hidden="true">
      <path d="M54 42 L905 42"/>
      <path d="M1020 42 L1146 42 L1146 636"/>
      <path d="M54 42 L54 636 L810 636"/>
      <path d="M1100 636 L1146 636"/>
    </svg>

    <div class="rider-artwork" role="img" aria-label="Broad-lined outline illustration of a dressage horse and rider in top hat and tailcoat"></div>
    <div class="hoof-artwork" role="img" aria-label="Horse hooves extending below the frame"></div>

    <section class="contact-block">
      <h1 class="trainer-name">DALE FERRIN</h1>
      <p class="trainer-phone">612-374-2059</p>
      <p class="services">CLASSICAL DRESSAGE TRAINING FOR THE MODERN AMERICAN<br>CLINICS, LESSONS, TRAINING LEVEL -PRIX ST. GEORGE</p>
    </section>
  </main>
</body>
</html>
```